Bram Keystone Homes needs a business card

We need a business card for a new company in Canada, Ontario. Our company is all about luxury contraction homes for our clients. Our product and services are custom projects design. Under the business logo that will be created, we want a slogan that will be a memorable phrase for consumers to remember us to tell their friends and relatives.

Additional infomation
- Ludovic Entrasse
- President / Ceo
-519.604.3087

Find point what luxury construction products and services can be done

We like to see colors:
- #663300
- and something other colors or color that would attract the client needs and wants

The final design should communicate leads from new or old clients that will grow our empire. Most of all, we try to work among the budget that clients want

NOTE
- we also need an icon for the business (Example: Instagram, Facebook, and Whatsapp icons)
- We want the company name to be remembered easily for clients and our distributors who would get our orders.
- we need an icon on the business cards: Facebook and Instagram.

Thanks,
Bram Keystone Homes

```html
<!DOCTYPE html>
<html lang="en">
<head>
<meta charset="utf-8">
<title>Bram Keystone Homes – Business Card</title>
<link rel="stylesheet" href="https://fonts.googleapis.com/css2?family=Poppins:wght@400;600;700&family=Roboto+Condensed:wght@700&display=swap">
<style>
  :root {
    --brand-brown: #663300;
    --text-grey: #4a4a4a;
    --card-white: #ffffff;
    --backdrop: #1c1c1c;
  }
  * { box-sizing: border-box; margin: 0; padding: 0; }
  html, body {
    width: 1200px;
    height: 874px;
    overflow: hidden;
    background: var(--backdrop);
  }
  .canvas {
    position: relative;
    width: 1200px;
    height: 874px;
  }
  .card {
    position: absolute;
    left: 320px;
    width: 560px;
    height: 320px;
    background: var(--card-white);
  }
  .card--front { top: 97px; }
  .card--back { top: 457px; }

  .wordmark {
    color: var(--brand-brown);
    font-family: "Poppins", sans-serif;
    font-weight: 700;
    line-height: 1;
    white-space: nowrap;
  }
  .tagline {
    color: var(--brand-brown);
    font-family: "Roboto Condensed", sans-serif;
    font-weight: 700;
    text-transform: uppercase;
    white-space: nowrap;
  }

  .card--front .brand-block {
    position: absolute;
    top: 104px;
    left: 0;
    width: 100%;
    text-align: center;
  }
  .card--front .wordmark { font-size: 40px; }
  .card--front .tagline { font-size: 15px; margin-top: 6px; }

  .social-row {
    position: absolute;
    top: 240px;
    left: 0;
    width: 100%;
    display: flex;
    justify-content: center;
    gap: 6px;
  }
  .social-dot {
    width: 28px;
    height: 28px;
    border: 1.5px solid var(--brand-brown);
    border-radius: 50%;
  }

  .card--back .brand-block {
    position: absolute;
    top: 72px;
    right: 40px;
    text-align: right;
  }
  .card--back .wordmark { font-size: 28px; }
  .card--back .tagline { font-size: 11px; margin-top: 4px; }

  .contact {
    position: absolute;
    left: 44px;
    top: 190px;
    font-family: "Poppins", sans-serif;
  }
  .contact__name {
    color: var(--brand-brown);
    font-size: 21px;
    font-weight: 400;
  }
  .contact__role,
  .contact__phone {
    color: var(--text-grey);
    font-size: 17px;
    line-height: 1.35;
  }
</style>
</head>
<body>
<main class="canvas">
  <section class="card card--front">
    <div class="brand-block">
      <p class="wordmark">Bram Keystone Homes</p>
      <p class="tagline">- Home Renovations - Custom Project Design -</p>
    </div>
    <div class="social-row" aria-label="Social media">
      <span class="social-dot"></span>
      <span class="social-dot"></span>
      <span class="social-dot"></span>
    </div>
  </section>

  <section class="card card--back">
    <div class="brand-block">
      <p class="wordmark">Bram Keystone Homes</p>
      <p class="tagline">- Home Renovations - Custom Project Design -</p>
    </div>
    <div class="contact">
      <p class="contact__name">Ludovic Entrasse</p>
      <p class="contact__role">President / Ceo</p>
      <p class="contact__phone">519.604.3087</p>
    </div>
  </section>
</main>
</body>
</html>
```